Retail Sign for Houseplant Campaign

Sign will measure 3 to 4 foot tall by 22.2inches and place on rolling racks of houseplants for a retail promotion in The Birchwell Yard. The theme of the promotion will be "New Year, New You!" Selling points which should be on the sign are Houseplants give you a taste of nature, Houseplants boost air quality inside your home, Indoor plants reduce anxiety, Indoor plants make you more productive, Houseplants improve your concentration and memory.
Updates

Target Market(s)

People who love plants

Industry/Entity Type

Horticulture/ retail

Colors
00AB8E
00BBA5
67D7C9
C6EFE9
E9F9F6
59FF00
82FF00
B8FF75
E3FFCB
F4FFEA
FFF300
FFF600
FEFA6F
FFFEC7
FFFEE8

Requirements
Must have
• Must feel energetic and encourage people to buy plants. Should include 1-2 photos and the selling points listed

```html
<!DOCTYPE html>
<html lang="en">
<head>
<meta charset="utf-8">
<title>New Year, New You! – Houseplant Sign</title>
<link rel="stylesheet" href="https://fonts.googleapis.com/css2?family=Raleway:wght@500;800&family=EB+Garamond:ital@1&display=swap">
<style>
  :root {
    --page: #ffffff;
    --rule: #dcdcdc;
    --title: #106873;
    --accent-bar: #00ab8e;
    --teal-deep: #178f7b;
    --teal-bright: #00b49c;
    --olive: #8a8126;
    --forest: #0b861b;
    --brand: #3b4a25;
    --ink-light: #ffffff;
  }
  * { box-sizing: border-box; margin: 0; padding: 0; }
  html, body { width: 793px; height: 1200px; overflow: hidden; background: var(--page); }
  .sign {
    position: absolute; left: 48px; top: 86px; width: 662px; height: 1071px;
    border: 1px solid var(--rule); background: var(--page);
  }
  .sign__topbar {
    position: absolute; left: 177px; top: -1px; width: 301px; height: 7px;
    background: var(--accent-bar);
  }
  .sign__title {
    position: absolute; left: 0; right: 0; top: 38px; text-align: center;
    font-family: "Raleway", sans-serif; font-weight: 800; font-size: 47px;
    letter-spacing: -1.2px; color: var(--title);
  }
  .grid {
    position: absolute; left: -1px; top: 130px; width: 662px; height: 855px;
    display: grid; grid-template-columns: 331px 331px; grid-template-rows: 213px 214px 214px 214px;
  }
  .cell { position: relative; overflow: hidden; }
  .point {
    display: flex; align-items: center; justify-content: center; text-align: center;
    font-family: "EB Garamond", serif; font-style: italic; font-size: 30px;
    line-height: 38.5px; color: var(--ink-light); padding: 0 20px;
  }
  .point--teal-deep { background: var(--teal-deep); }
  .point--teal-bright { background: var(--teal-bright); }
  .point--olive { background: var(--olive); }
  .point--forest { background: var(--forest); }
  .photo--crouton { background: linear-gradient(120deg, #f2f4f3 0%, #e6e2dc 55%, #b9a48c 80%, #8e8f93 100%); }
  .photo--monstera { background: linear-gradient(100deg, #3f3228 0%, #efeae6 30%, #f4f1ee 55%, #2f5a2c 75%, #16351a 100%); }
  .photo--snake-plant { background: linear-gradient(110deg, #e9e9ea 0%, #d9d6d4 35%, #5f8f9a 60%, #3d5a3c 85%, #9a9a9a 100%); }
  .photo--relaxing { background: linear-gradient(100deg, #eef0ee 0%, #9fb28a 25%, #f3efec 50%, #d7b7b6 70%, #3f5378 100%); }
  .edge-tab { position: absolute; width: 12px; height: 121px; }
  .edge-tab--right { right: 0; }
  .edge-tab--left { left: 0; }
  .brands {
    position: absolute; left: 0; right: 0; top: 1000px; height: 48px;
    display: flex; align-items: center; justify-content: center; gap: 14px;
    font-family: "Raleway", sans-serif; font-weight: 500; color: var(--brand);
  }
  .brand { display: flex; align-items: center; gap: 8px; font-size: 22px; letter-spacing: 0.3px; }
  .brand__mark { width: 26px; height: 26px; background: var(--brand); }
  .brands__divider { width: 1px; height: 34px; background: var(--brand); opacity: 0.5; }
</style>
</head>
<body>
  <main class="sign">
    <div class="sign__topbar"></div>
    <h1 class="sign__title">New Year, New You!</h1>

    <section class="grid">
      <p class="cell point point--teal-deep">Houseplants<br>give you a taste<br>of nature</p>
      <div class="cell photo--crouton" role="img" aria-label="Woman placing a potted croton plant on a white shelf in a bright living room">
        <span class="edge-tab edge-tab--right" style="top:44px;background:var(--teal-deep)"></span>
      </div>

      <div class="cell photo--monstera" role="img" aria-label="Smiling woman wiping the leaves of a large monstera plant">
        <span class="edge-tab edge-tab--left" style="top:46px;background:var(--teal-bright)"></span>
      </div>
      <p class="cell point point--teal-bright">Houseplants<br>boost air quality<br>inside your home</p>

      <p class="cell point point--olive">Indoor plants<br>reduce anxiety,<br>Indoor plants make<br>you more productive</p>
      <div class="cell photo--snake-plant" role="img" aria-label="Mother and daughter watering a snake plant with a turquoise watering can">
        <span class="edge-tab edge-tab--right" style="top:47px;background:var(--olive)"></span>
      </div>

      <div class="cell photo--relaxing" role="img" aria-label="Woman relaxing on the floor beside a laptop, surrounded by houseplants">
        <span class="edge-tab edge-tab--left" style="top:47px;background:var(--forest)"></span>
      </div>
      <p class="cell point point--forest">Houseplants<br>improve your<br>concentration<br>and memory</p>
    </section>

    <footer class="brands">
      <span class="brand"><span class="brand__mark"></span>Verdant Hollow</span>
      <span class="brands__divider"></span>
      <span class="brand">The Birchwell Yard</span>
    </footer>
  </main>
</body>
</html>
```